Veltrano.co - Polar Expeditions Specialists

We need a modern, visually striking business card for Veltrano.co, a company specialized in selling expedition cruises to the most remote regions on Earth, with a focus on the Arctic and Antarctica. The design should instantly communicate that the cardholder is an expert in polar travel. Use clean, premium aesthetics with cool tones like icy blue and white, possibly incorporating polar imagery (ice, glaciers, penguins, etc.)

Attached the logo

Contact Information for Business Card

Feels high-end and trustworthy.. Visually memorable — encourages people to keep it

Colors
0054AA
0677BA
7BADD7
CADEEF
E8F1F8

Requirements
Must have
• ice, glaciers, penguins, montains
Nice to have
• modern, transparente,

```html
<!DOCTYPE html>
<html lang="en">
<head>
<meta charset="utf-8">
<title>Veltrano.co Business Card</title>
<link rel="stylesheet" href="https://fonts.googleapis.com/css2?family=Poppins:wght@400;500;600;700;800&display=swap">
<style>
  :root {
    --page-bg: #e3e8ea;
    --card-blue: #2c78bb;
    --navy-light: #343a58;
    --navy-dark: #0f1a33;
    --white: #ffffff;
  }
  * { margin: 0; padding: 0; box-sizing: border-box; }
  html, body { width: 1200px; height: 960px; overflow: hidden; }
  body {
    background: var(--page-bg);
    font-family: "Poppins", sans-serif;
    position: relative;
  }
  .card {
    position: absolute;
    top: 105px;
    width: 430px;
    height: 750px;
    border-radius: 26px;
    overflow: hidden;
  }
  /* Front */
  .card-front { left: 142px; }
  .front-scene {
    position: absolute; inset: 0;
    background: linear-gradient(100deg, var(--navy-light) 0%, #2b3350 45%, #1d2944 70%, var(--navy-dark) 100%);
  }
  .front-brand, .front-tagline {
    position: absolute;
    color: var(--white);
    white-space: nowrap;
    transform: translate(-50%, -50%) rotate(-90deg);
  }
  .front-brand {
    left: 286px; top: 375px;
    font-size: 70px; font-weight: 800; letter-spacing: -1px; line-height: 1;
  }
  .front-tagline {
    left: 341px; top: 375px;
    font-size: 22px; font-weight: 500; line-height: 1;
  }
  /* Back */
  .card-back { left: 631px; background: var(--card-blue); color: var(--white); text-align: center; }
  .back-top {
    position: absolute; left: 0; top: 0; width: 100%; height: 252px;
    background: var(--white);
  }
  .back-brand {
    position: absolute; left: 0; width: 100%; top: 22px;
    color: var(--card-blue); font-size: 50px; font-weight: 800; letter-spacing: -0.5px; line-height: 1.2;
  }
  .back-tagline {
    position: absolute; left: 0; width: 100%; top: 82px;
    color: var(--card-blue); font-size: 15px; font-weight: 600;
  }
  .brand-dot {
    position: absolute; left: 135px; top: 150px;
    width: 160px; height: 160px; border-radius: 50%;
    background: var(--card-blue);
    border: 4px solid var(--white);
  }
  .holder-name {
    position: absolute; left: 0; width: 100%; top: 410px;
    font-size: 38px; line-height: 1.2;
  }
  .holder-name .first { font-weight: 700; }
  .holder-name .last { font-weight: 400; }
  .holder-role {
    position: absolute; left: 0; width: 100%; top: 462px;
    font-size: 19px; font-weight: 500;
  }
  .divider { position: absolute; left: 15px; width: 400px; height: 34px; }
  .divider-contact { top: 503px; }
  .divider-address { top: 626px; }
  .contact-list, .address {
    position: absolute; left: 0; width: 100%;
    font-size: 20px; font-weight: 400; line-height: 27.5px; list-style: none;
  }
  .contact-list { top: 540px; }
  .address { top: 661px; font-style: normal; }
</style>
</head>
<body>
  <section class="card card-front">
    <div class="front-scene" role="img" aria-label="Dark navy-toned photo of icebergs floating on polar water"></div>
    <div class="front-brand">Veltrano.co</div>
    <div class="front-tagline">Polar Expeditions Specialists</div>
  </section>

  <section class="card card-back">
    <div class="back-top"></div>
    <div class="back-brand">Veltrano.co</div>
    <div class="back-tagline">Polar Expeditions Specialists</div>
    <div class="brand-dot"></div>

    <div class="holder-name"><span class="first">Marta</span> <span class="last">Lindqvist</span></div>
    <div class="holder-role">Founder &amp; CEO</div>

    <svg class="divider divider-contact" viewBox="0 0 400 34" aria-hidden="true">
      <g fill="#fff">
        <circle cx="4" cy="17" r="3.5"/><circle cx="25" cy="17" r="4.5"/><circle cx="46" cy="17" r="5.5"/>
        <circle cx="67" cy="17" r="6.5"/><circle cx="88" cy="17" r="7.5"/><circle cx="109" cy="17" r="8.5"/><circle cx="130" cy="17" r="9"/>
        <circle cx="270" cy="17" r="9"/><circle cx="291" cy="17" r="8.5"/><circle cx="312" cy="17" r="7.5"/><circle cx="333" cy="17" r="6.5"/>
        <circle cx="354" cy="17" r="5.5"/><circle cx="375" cy="17" r="4.5"/><circle cx="396" cy="17" r="3.5"/>
        <circle cx="163" cy="17" r="15"/><circle cx="200" cy="17" r="15"/><circle cx="237" cy="17" r="15"/>
      </g>
      <path d="M157 10c1-1 2-1 3 0l2 3-2 2c1 2 3 4 5 5l2-2 3 2c1 1 1 2 0 3-2 2-5 2-8 0-3-2-5-4-6-7-1-3 0-5 1-6z" fill="#2c78bb"/>
      <g fill="none" stroke="#2c78bb" stroke-width="1.8">
        <rect x="191" y="11" width="18" height="13" rx="1.5"/>
        <path d="M191 12l9 7 9-7"/>
        <circle cx="237" cy="17" r="8"/>
        <path d="M229 17h16M237 9c-4 5-4 11 0 16M237 9c4 5 4 11 0 16"/>
      </g>
    </svg>

    <ul class="contact-list">
      <li>(512) 555-0148</li>
      <li>hello@veltrano.co</li>
      <li>www.veltrano.co</li>
    </ul>

    <svg class="divider divider-address" viewBox="0 0 400 34" aria-hidden="true">
      <g fill="#fff">
        <circle cx="4" cy="17" r="3.5"/><circle cx="25" cy="17" r="4.5"/><circle cx="46" cy="17" r="5.5"/>
        <circle cx="67" cy="17" r="6.5"/><circle cx="88" cy="17" r="7.5"/><circle cx="112" cy="17" r="8.5"/>
        <circle cx="135" cy="17" r="9"/><circle cx="163" cy="17" r="10"/>
        <circle cx="237" cy="17" r="10"/><circle cx="265" cy="17" r="9"/><circle cx="288" cy="17" r="8.5"/>
        <circle cx="312" cy="17" r="7.5"/><circle cx="333" cy="17" r="6.5"/><circle cx="354" cy="17" r="5.5"/>
        <circle cx="375" cy="17" r="4.5"/><circle cx="396" cy="17" r="3.5"/>
        <circle cx="200" cy="17" r="15"/>
      </g>
      <g fill="none" stroke="#2c78bb" stroke-width="1.8">
        <path d="M200 27c-4-5-6-8-6-11a6 6 0 0 1 12 0c0 3-2 6-6 11z"/>
        <circle cx="200" cy="15.5" r="2"/>
      </g>
    </svg>

    <address class="address">
      1740 Harbor Ridge Rd. Suite 310<br>
      Austin, TX 78701
    </address>
  </section>
</body>
</html>
```